US company needs luxury product packaging design for a line of hair extensions

What we Need:
Design product packaging for our top of the line hair extension product called Verosina™, the design should have the Verosina™ name,and the head from our Dovetress logo on the box.

Who we are
Our company DoveTress™ is a wholesaler of 100% human hair extensions. We sell the best quality double drawn hair wefts, clip-ins and wigs.

The detailed brief is in the attached word document with examples of packaging we like and we have also uploaded our company logo

The winning designer(s) will work with us on 9 other products packages that we need, so it is important to think strategically

Thanks

Target Market(s)

African American Women

Industry/Entity Type

Hair And Beauty

Font styles to use
Serif
Decorative
Script

Colors
fbf289
b768aa
e24096
000000
fbd4d5
f59195
ffc214
d3a5cc
eda3c7

Requirements
Must have
• Evoke luxury
Nice to have
• See Attached brief

```html
<!DOCTYPE html>
<html lang="en">
<head>
<meta charset="utf-8">
<title>Lumera Drawer Slider Rigid Box – Dielines</title>
<link href="https://fonts.googleapis.com/css2?family=Arimo&family=Cormorant+Garamond:wght@600&family=Great+Vibes&display=swap" rel="stylesheet">
<style>
  :root {
    --canvas-grey: #b3b3b3;
    --ink: #111111;
    --royal-purple: #5c0084;
    --deep-plum: #2b0042;
    --night-plum: #12001c;
    --black: #000000;
    --white: #ffffff;
    --blush: #fbd4d5;
    --rule-grey: #555555;
    --magenta: #e24096;
    --rose: #b01257;
    --muted-line: #6b4a7a;
  }
  html, body {
    margin: 0;
    padding: 0;
    width: 1200px;
    height: 1200px;
    overflow: hidden;
    background: var(--canvas-grey);
  }
  .sheet { display: block; width: 1200px; height: 1200px; }
  .spec-block { font-family: "Arimo", Arial, sans-serif; fill: var(--ink); font-size: 11px; }
  .spec-title { font-size: 12.5px; }
  .brand-name {
    font-family: "Cormorant Garamond", Georgia, serif;
    font-weight: 600;
    letter-spacing: 2px;
    fill: var(--blush);
  }
  .tagline { font-family: "Great Vibes", cursive; fill: var(--blush); }
  .fine-print { font-family: "Arimo", Arial, sans-serif; fill: #cfc3d6; font-size: 3.6px; }
  .insert-copy { font-family: "Arimo", Arial, sans-serif; fill: #333333; font-size: 3.3px; }
  .insert-heading { font-family: "Arimo", Arial, sans-serif; fill: #333333; font-size: 3.4px; letter-spacing: 0.3px; }
</style>
</head>
<body>
<svg class="sheet" viewBox="0 0 1200 1200" xmlns="http://www.w3.org/2000/svg">
  <defs>
    <linearGradient id="tray-column" x1="0" y1="0" x2="0" y2="1">
      <stop offset="0" stop-color="var(--black)"/>
      <stop offset="0.25" stop-color="var(--royal-purple)"/>
      <stop offset="0.75" stop-color="var(--royal-purple)"/>
      <stop offset="1" stop-color="var(--black)"/>
    </linearGradient>
    <linearGradient id="tray-flap-left" x1="0" y1="0" x2="1" y2="0">
      <stop offset="0" stop-color="var(--black)"/>
      <stop offset="1" stop-color="var(--royal-purple)"/>
    </linearGradient>
    <linearGradient id="tray-flap-right" x1="0" y1="0" x2="1" y2="0">
      <stop offset="0" stop-color="var(--royal-purple)"/>
      <stop offset="1" stop-color="var(--black)"/>
    </linearGradient>
    <linearGradient id="liner-band" x1="0" y1="0" x2="1" y2="0">
      <stop offset="0" stop-color="var(--night-plum)"/>
      <stop offset="1" stop-color="var(--deep-plum)"/>
    </linearGradient>
    <linearGradient id="sleeve-panel" x1="0" y1="0" x2="0" y2="1">
      <stop offset="0" stop-color="var(--black)"/>
      <stop offset="1" stop-color="var(--deep-plum)"/>
    </linearGradient>
    <linearGradient id="sleeve-spine" x1="0" y1="0" x2="0" y2="1">
      <stop offset="0" stop-color="var(--night-plum)"/>
      <stop offset="1" stop-color="var(--deep-plum)"/>
    </linearGradient>
    <radialGradient id="artwork-fill" cx="0.5" cy="0.45" r="0.6">
      <stop offset="0" stop-color="var(--magenta)"/>
      <stop offset="1" stop-color="var(--rose)"/>
    </radialGradient>
  </defs>

  <!-- Spec block -->
  <g class="spec-block">
    <text class="spec-title" x="66" y="207">DRAWER SLIDER RIGID BOX</text>
    <text x="66" y="222">CUSTOMER:  CLIENT0417 (MARKETPLACE)</text>
    <text x="66" y="235">CAD DRAWING BUILT BY:</text>
    <text x="66" y="250">MARA DELLWYN (www.foldlinestudio.com)</text>
    <text x="66" y="262">DATE COMPLETED:  14 SEPT 2016</text>
    <text x="66" y="275">STYLE:  CUSTOM RIGID BOX</text>
    <text x="66" y="288">SIZE:  DRAWER - 10" X 8" X 3"</text>
    <text x="66" y="301">SLEEVE - 10.125" X 3.125" X 8.125"</text>
    <text x="66" y="315">MATERIAL:  .060 GAUGE PAPERBOARD THICKNESS</text>
  </g>

  <!-- Drawer tray wrap -->
  <g class="tray-wrap">
    <rect x="494" y="268" width="181" height="283" fill="url(#tray-column)"/>
    <polygon points="425,322 488,322 494,336 494,484 488,498 425,498" fill="url(#tray-flap-left)"/>
    <polygon points="681,322 745,322 745,498 681,498 675,484 675,336" fill="url(#tray-flap-right)"/>
  </g>

  <!-- Drawer liner -->
  <g class="tray-liner">
    <rect x="848" y="338" width="229" height="144" fill="var(--white)"/>
    <rect x="872" y="314" width="181" height="192" fill="var(--white)"/>
    <rect x="872" y="288" width="181" height="26" fill="url(#liner-band)"/>
    <rect x="872" y="506" width="181" height="25" fill="url(#liner-band)"/>
    <rect x="823" y="338" width="25" height="144" fill="url(#liner-band)"/>
    <rect x="1077" y="338" width="25" height="144" fill="url(#liner-band)"/>
    <rect x="875" y="340" width="176" height="140" rx="7" fill="var(--white)" stroke="var(--rule-grey)" stroke-width="2"/>

    <g class="insert-text-flipped" transform="rotate(180 963 370)">
      <line x1="913" y1="350" x2="1013" y2="350" stroke="#999" stroke-width="0.4"/>
      <text class="insert-heading" x="963" y="354" text-anchor="middle">ABOUT VEROSINA</text>
      <text class="insert-copy" x="963" y="360" text-anchor="middle">Verosina™ is an ultra-luxurious, high quality 100%</text>
      <text class="insert-copy" x="963" y="364" text-anchor="middle">human hair extension with all the cuticles intact.</text>
      <text class="insert-copy" x="963" y="368" text-anchor="middle">It has a natural texture and brilliant luster.</text>
      <text class="insert-copy" x="963" y="372" text-anchor="middle">It comes in many hair types, lengths and colors.</text>
      <text class="insert-copy" x="963" y="376" text-anchor="middle">It can be dyed, bleached or curled like your own hair.</text>
      <text class="insert-copy" x="963" y="380" text-anchor="middle">Every piece is hand inspected by our experts.</text>
      <line x1="913" y1="386" x2="1013" y2="386" stroke="#999" stroke-width="0.4"/>
    </g>

    <g class="insert-text">
      <text class="insert-heading" x="963" y="432" text-anchor="middle">ABOUT VEROSINA</text>
      <line x1="913" y1="435" x2="1013" y2="435" stroke="#999" stroke-width="0.4"/>
      <text class="insert-copy" x="963" y="441" text-anchor="middle">Verosina™ is an ultra-luxurious, high quality 100%</text>
      <text class="insert-copy" x="963" y="445" text-anchor="middle">human hair extension with all the cuticles intact.</text>
      <text class="insert-copy" x="963" y="449" text-anchor="middle">It has a natural texture and brilliant luster.</text>
      <text class="insert-copy" x="963" y="453" text-anchor="middle">It comes in many hair types, lengths and colors.</text>
      <text class="insert-copy" x="963" y="457" text-anchor="middle">It can be dyed, bleached or curled like your own hair.</text>
      <text class="insert-copy" x="963" y="461" text-anchor="middle">Every piece is hand inspected by our experts.</text>
      <line x1="913" y1="470" x2="1013" y2="470" stroke="#999" stroke-width="0.4"/>
    </g>
  </g>

  <!-- Sleeve -->
  <g class="sleeve">
    <!-- Back panel -->
    <polygon points="246,628 451,628 451,776 444,786 253,786 246,776" fill="url(#sleeve-panel)"/>
    <rect x="260" y="641" width="177" height="141" fill="none" stroke="var(--muted-line)" stroke-width="0.6"/>
    <text class="brand-name" x="349" y="710" font-size="20" text-anchor="middle">LUMERA</text>
    <text class="fine-print" x="349" y="718" text-anchor="middle">100% HUMAN HAIR EXTENSIONS</text>
    <line x1="295" y1="750" x2="403" y2="750" stroke="var(--muted-line)" stroke-width="0.5"/>
    <text class="fine-print" x="349" y="758" text-anchor="middle">Product of Dovetress LLC. All rights reserved.</text>
    <text class="fine-print" x="349" y="762.5" text-anchor="middle">Lumera name and Dovetress are trademarks of Dovetress</text>
    <text class="fine-print" x="349" y="767" text-anchor="middle">LLC., registered in the USA.</text>
    <line x1="295" y1="773" x2="403" y2="773" stroke="var(--muted-line)" stroke-width="0.5"/>

    <!-- Spine band -->
    <rect x="99" y="786" width="499" height="56" fill="url(#sleeve-spine)"/>
    <rect x="256" y="786" width="184" height="56" fill="var(--night-plum)" opacity="0.55"/>

    <g class="spine-label-left">
      <rect x="116" y="791" width="7" height="7" fill="#8a7a90"/>
      <circle cx="124" cy="830" r="5" fill="#8a7a90"/>
      <text class="brand-name" x="190" y="816" font-size="17" text-anchor="middle">LUMERA</text>
      <text class="tagline" x="190" y="828" font-size="6" text-anchor="middle">100% Human Hair Extensions</text>
    </g>
    <g class="spine-label-right">
      <rect x="566" y="791" width="7" height="7" fill="#8a7a90"/>
      <circle cx="574" cy="830" r="5" fill="#8a7a90"/>
      <text class="brand-name" x="505" y="816" font-size="17" text-anchor="middle">LUMERA</text>
      <text class="tagline" x="505" y="828" font-size="6" text-anchor="middle">100% Human Hair Extensions</text>
    </g>

    <!-- Front panel -->
    <polygon points="253,842 444,842 451,850 451,998 246,998 246,850" fill="url(#sleeve-panel)"/>
    <rect role="img" aria-label="Brand artwork area in sparkling magenta tones" x="310" y="848" width="80" height="88" rx="36" fill="url(#artwork-fill)"/>
    <text class="brand-name" x="349" y="957" font-size="17" text-anchor="middle">LUMERA</text>
    <text class="tagline" x="349" y="968" font-size="6" text-anchor="middle">100% Human Hair Extensions</text>
    <line x1="300" y1="977" x2="398" y2="977" stroke="var(--muted-line)" stroke-width="0.5"/>
  </g>

  <!-- Sleeve inner lining -->
  <g class="sleeve-lining">
    <rect x="844" y="648" width="182" height="339" fill="var(--white)"/>
    <rect x="702" y="788" width="467" height="58" fill="var(--white)"/>
  </g>
</svg>
</body>
</html>
```